Brightfen Business Card Redesign & Logo Update

We need to update our business cards to something more modern and fresh. Brightfen can provide the current color schemes and old design examples, but welcome creativity in helping us with this redesign. PLEASE NOTE that we no longer utilize the "tree" and/or "leaf" imagery in our branding. If able would apprecaite an update on the quality of our "words only" logo in Ai. / PNG formats too.

Target Market(s)

Investors, landowners, corporate partners, contractors

Industry/Entity Type

Environmental Restoration & Conservation

Contact Information for Business Card

Logo, persons name, title, mailing address, phone and email, website url

Font styles to use
Other font styles liked:
• Merriweather

Requirements
Nice to have
• Logo, persons name, title, mailing address, phone and email, website url, but open to ideams
Should not have
• No all back backgrounds

```html
<!DOCTYPE html>
<html lang="en">
<head>
<meta charset="utf-8">
<title>Brightfen Business Card</title>
<link rel="stylesheet" href="https://fonts.googleapis.com/css2?family=Oswald:wght@500;700&family=Open+Sans:wght@400;700&display=swap">
<style>
  :root {
    --bg: #e9eaec;
    --card: #ffffff;
    --orange: #ee7d22;
    --green: #137e3f;
    --ink: #111111;
    --shadow: rgba(0, 0, 0, 0.18);
  }
  * { box-sizing: border-box; margin: 0; padding: 0; }
  html, body {
    width: 1200px; height: 780px; overflow: hidden;
    background: var(--bg);
  }
  .sheet {
    width: 1200px; height: 780px;
    display: flex; align-items: center; justify-content: center; gap: 40px;
  }
  .card {
    position: relative;
    width: 540px; height: 309px;
    background: var(--card);
    box-shadow: 0 10px 28px var(--shadow);
    overflow: hidden;
  }
  .card-bands { position: absolute; inset: 0; width: 100%; height: 100%; }
  .band-orange { fill: var(--orange); }
  .band-green { fill: var(--green); }

  .wordmark { position: absolute; font-family: "Oswald", sans-serif; line-height: 1; }
  .wordmark-name {
    display: block; color: var(--green); font-weight: 700;
    text-transform: uppercase; letter-spacing: 1px;
  }
  .wordmark-tagline {
    display: block; color: var(--ink); font-weight: 500;
    text-transform: uppercase; letter-spacing: 0.5px;
  }

  .card-back .wordmark { left: 0; right: 0; top: 78px; text-align: center; }
  .card-back .wordmark-name { font-size: 88px; }
  .card-back .wordmark-tagline { font-size: 22px; margin-top: 6px; }

  .card-front .wordmark { left: 34px; top: 108px; width: 240px; text-align: center; }
  .card-front .wordmark-name { font-size: 52px; }
  .card-front .wordmark-tagline { font-size: 13px; margin-top: 4px; }

  .divider {
    position: absolute; left: 292px; top: 70px;
    width: 2px; height: 130px; background: var(--ink);
  }
  .contact {
    position: absolute; left: 318px; top: 66px;
    font-family: "Open Sans", sans-serif; color: var(--ink);
  }
  .contact-name { font-size: 21px; font-weight: 700; line-height: 1.1; }
  .contact-name .first { color: var(--orange); }
  .contact-name .last { color: var(--green); }
  .contact-title { font-size: 13px; margin-top: 3px; }
  .contact-list { list-style: none; margin-top: 20px; }
  .contact-list li {
    display: flex; align-items: center; gap: 8px;
    font-size: 12.5px; line-height: 1; margin-bottom: 8px;
  }
  .contact-icon { width: 13px; height: 13px; flex: none; }
  .contact-icon .ic { fill: var(--orange); }
  .contact-icon .ic-line { fill: none; stroke: #fff; stroke-width: 1.2; }
</style>
</head>
<body>
<main class="sheet">

  <section class="card card-back" aria-label="Card back">
    <svg class="card-bands" viewBox="0 0 540 309" aria-hidden="true">
      <polygon class="band-orange" points="540,248 280,248 272,258 160,258 145,276 540,276"/>
      <polygon class="band-green" points="0,282 262,282 270,270 276,270 266,288 0,288"/>
    </svg>
    <div class="wordmark">
      <span class="wordmark-name">Brightfen</span>
      <span class="wordmark-tagline">Environmental Credit Company</span>
    </div>
  </section>

  <section class="card card-front" aria-label="Card front">
    <svg class="card-bands" viewBox="0 0 540 309" aria-hidden="true">
      <polygon class="band-orange" points="540,248 280,248 272,258 160,258 145,276 540,276"/>
      <polygon class="band-green" points="0,282 262,282 270,270 276,270 266,288 0,288"/>
    </svg>

    <div class="wordmark">
      <span class="wordmark-name">Brightfen</span>
      <span class="wordmark-tagline">Environmental Credit Company</span>
    </div>

    <div class="divider"></div>

    <div class="contact">
      <p class="contact-name"><span class="first">Marta</span> <span class="last">Delcourt</span></p>
      <p class="contact-title">Managing Director</p>
      <ul class="contact-list">
        <li>
          <svg class="contact-icon" viewBox="0 0 14 14" aria-hidden="true">
            <circle class="ic" cx="7" cy="7" r="7"/>
            <path class="ic-line" d="M4.5 4 Q4 7 7 9.5 Q8.5 10.5 9.8 9.6 L8.6 8.3 Q7.6 8.7 6.5 7.5 Q5.3 6.4 5.7 5.4 Z"/>
          </svg>
          (555) 214-0387
        </li>
        <li>
          <svg class="contact-icon" viewBox="0 0 14 14" aria-hidden="true">
            <circle class="ic" cx="7" cy="7" r="7"/>
            <rect class="ic-line" x="3.5" y="4.5" width="7" height="5"/>
            <path class="ic-line" d="M3.5 4.5 L7 7.3 L10.5 4.5"/>
          </svg>
          info@brightfen.com
        </li>
        <li>
          <svg class="contact-icon" viewBox="0 0 14 14" aria-hidden="true">
            <circle class="ic" cx="7" cy="7" r="7"/>
            <circle class="ic-line" cx="7" cy="7" r="3.8"/>
            <path class="ic-line" d="M3.2 7 H10.8 M7 3.2 Q5 7 7 10.8 Q9 7 7 3.2"/>
          </svg>
          www.brightfen.com
        </li>
      </ul>
    </div>
  </section>

</main>
</body>
</html>
```